CM Candle Tube Packaging Design

Website: www.corvelmare.example
IG: @corvel.mare
Tagline: Elevate Your Ambiance
My brand is a sophisticated brand with luxury candles made of coconut wax. Im looking for an upscale minimalist chic design.
Discover the transformative power of positive energy with Corvel Mare candles. Indulge in true luxury with our specially crafted coconut wax blend that not only ignites captivating scents but also embodies modern elegance and empowering elements.
At Corvel Mare we're committed to delivering a unique and exhilarating aromatic experience to all candle lovers. Each candle is meticulously handcrafted in small batches using luxury fragrance oils exclusively formulated for coconut wax.
Our candles are:
Clean-burning
Paraben-Free
Phthalate-Free
Skin-Safe
Pet-Friendly

```html
<!DOCTYPE html>
<html lang="en">
<head>
<meta charset="utf-8">
<title>Corvel Mare — Candle Tube Packaging</title>
<link rel="stylesheet" href="https://fonts.googleapis.com/css2?family=Poiret+One&family=Montserrat:wght@400;500&family=Allura&display=swap">
<style>
  :root {
    --backdrop: #f0dfe1;
    --tube-pink-light: #eebcbb;
    --tube-pink-deep: #d8a4a4;
    --band-white: #f7f1f1;
    --band-pink: #ecc9ca;
    --ink: #1b1718;
    --label-white: #f8f6f6;
    --lid-white: #f3f3f5;
    --lid-rim: #ffffff;
  }
  * { margin: 0; padding: 0; box-sizing: border-box; }
  html, body {
    width: 1200px;
    height: 1107px;
    overflow: hidden;
    background: var(--backdrop);
  }
  .canvas {
    position: relative;
    width: 1200px;
    height: 1107px;
  }
  .tube-wrap {
    position: absolute;
    left: 110px;
    top: 200px;
    width: 445px;
    height: 790px;
  }
  .pattern-band {
    width: 100%;
    height: 230px;
    background: linear-gradient(180deg, var(--band-white), var(--band-pink));
  }
  .tube-body {
    position: relative;
    width: 100%;
    height: 560px;
    background: linear-gradient(90deg, var(--tube-pink-light), var(--tube-pink-deep) 70%, var(--tube-pink-light));
    text-align: center;
    color: var(--ink);
  }
  .brand-name {
    position: absolute;
    top: 155px;
    left: 0;
    width: 100%;
    font-family: "Poiret One", sans-serif;
    font-size: 50px;
    letter-spacing: 1px;
    line-height: 1;
  }
  .product-line {
    position: absolute;
    top: 230px;
    left: 0;
    width: 100%;
    display: flex;
    align-items: center;
    justify-content: center;
    gap: 14px;
    font-family: "Montserrat", sans-serif;
    font-size: 13px;
    letter-spacing: 5px;
  }
  .product-line .rule {
    display: block;
    width: 20px;
    height: 1px;
    background: var(--ink);
  }
  .product-line .label { margin-right: -5px; }
  .script-line {
    position: absolute;
    top: 262px;
    left: 0;
    width: 100%;
    font-family: "Allura", cursive;
    font-size: 20px;
  }
  .tagline-label {
    position: absolute;
    top: 385px;
    left: 94px;
    width: 270px;
    height: 34px;
    background: var(--label-white);
    font-family: "Montserrat", sans-serif;
    font-size: 12px;
    letter-spacing: 4px;
    line-height: 34px;
    font-style: italic;
  }
  .net-weight {
    position: absolute;
    top: 498px;
    left: 0;
    width: 100%;
    font-family: "Montserrat", sans-serif;
    font-weight: 500;
    font-size: 13px;
  }
  .lid {
    position: absolute;
    left: 642px;
    top: 395px;
    width: 434px;
    height: 434px;
    border-radius: 50%;
    background: var(--lid-white);
    border: 12px solid var(--lid-rim);
    display: flex;
    align-items: center;
    justify-content: center;
  }
  .lid-monogram {
    font-family: "Poiret One", sans-serif;
    font-size: 96px;
    color: var(--ink);
    line-height: 1;
  }
</style>
</head>
<body>
  <main class="canvas">
    <section class="tube-wrap">
      <div class="pattern-band" role="img" aria-label="Repeating pattern of small pink flame outlines on white"></div>
      <div class="tube-body">
        <h1 class="brand-name">CORVEL MARE</h1>
        <p class="product-line"><span class="rule"></span><span class="label">HANDMADE CANDLES</span><span class="rule"></span></p>
        <p class="script-line">with purpose and love</p>
        <p class="tagline-label">Elevate Your Ambiance</p>
        <p class="net-weight">9 OZ/255G</p>
      </div>
    </section>
    <section class="lid">
      <span class="lid-monogram">CM</span>
    </section>
  </main>
</body>
</html>
```